FinTech company looking to revamp and expand client-facing interface for our financial models

Pellworth Engines currently has a very simple website that allows clients to interact with our financial models. We are looking to completely redesign the current site and add several extra pages to provide extra functionality. We want the design to have a modern, slick feel, that will work on both a desktop or a tablet. It should be straightforward for clients to move between different pages at any time, and clear from the layout how to interact with the more advanced features. We have included screenshots of existing pages in the attached design brief, as well as sketches of the functionality required by the new pages, but can't provide a direct link to the current site.
Target Market(s)
Professional investors that will be paying to access the interface
Industry/Entity Type
Finance
Number of Pages Required
4 page
Colors
Designer to choose colors to be used in the design.
Look and feel
Each slider illustrates characteristics of the customer's brand and the style your logo design should communicate.

```html
<!DOCTYPE html>
<html lang="en">
<head>
<meta charset="utf-8">
<title>Pellworth Engines – Models</title>
<link href="https://fonts.googleapis.com/css2?family=Poppins:wght@300;400;600;700&display=swap" rel="stylesheet">
<style>
:root{
  --navy:#00305f;
  --page:#f0eff0;
  --white:#ffffff;
  --row-alt:#dce6fa;
  --line:#d9d9d9;
  --ink:#1d1d1d;
  --muted:#6b6b6b;
  --icon:#3d8bf5;
}
*{box-sizing:border-box;margin:0;padding:0}
html,body{width:1172px;height:1200px;overflow:hidden;background:var(--page);font-family:'Poppins',sans-serif;color:var(--ink)}
.stage{position:absolute;left:0;top:0;width:1440px;height:1474px;transform:scale(0.81389);transform-origin:0 0}
.panel{position:absolute;left:20px;width:1400px;background:var(--white);box-shadow:0 1px 3px rgba(0,0,0,.18)}
.panel--models{top:20px;height:730px}
.panel--factors{top:805px;height:632px}
.topbar{position:absolute;left:0;top:17px;width:1400px;height:68px;background:var(--navy);color:var(--white);font-weight:600;font-size:15px}
.topbar span{position:absolute;top:0;line-height:68px}
.brand{font-size:21px;font-weight:700;letter-spacing:.2px}
.tab-active{background:var(--white);color:var(--navy);height:68px;text-align:center}
.dropdown{position:absolute;left:985px;top:85px;width:108px;height:163px;background:var(--white);box-shadow:0 2px 4px rgba(0,0,0,.15);font-size:15px;padding:7px 0 0 25px}
.dropdown div{height:31px;line-height:22px}
.label{position:absolute;font-size:19px;font-weight:400}
.label b{font-weight:600}
.field{position:absolute;height:36px;border:1px solid #cfcfcf;border-radius:4px;box-shadow:0 1px 2px rgba(0,0,0,.12);font-size:16px;line-height:34px;padding-left:17px}
.export{position:absolute;font-size:16px;display:flex;align-items:center;gap:10px}
table{position:absolute;left:29px;border-collapse:collapse;table-layout:fixed;font-size:16px;font-weight:300}
th{background:var(--navy);color:var(--white);font-weight:600;font-size:17px;border-right:1px solid #2a4f7a}
th:last-child{border-right:none}
td{text-align:center;border:1px solid var(--line);color:var(--muted);line-height:25px}
td.id{color:var(--ink);font-weight:400}
td.num{color:#555}
tbody tr:nth-child(even) td{background:var(--row-alt)}
.models th{height:58px}
.models td{height:69px}
.factors th{height:59px}
.factors td{height:50px}
.footer{position:absolute;left:0;width:1400px;text-align:center;font-size:17px}
.code{position:absolute;font-size:14px}
</style>
</head>
<body>
<div class="stage">

<section class="panel panel--models">
  <header class="topbar">
    <span class="brand" style="left:30px">PELLWORTH</span>
    <span style="left:500px">QBOSS</span>
    <span class="tab-active" style="left:572px;width:68px">250D</span>
    <span style="left:665px">83D</span>
    <span style="left:732px">42D</span>
    <span class="tab-active" style="left:985px;width:108px">MODELS</span>
    <span style="left:1100px">|</span>
    <span style="left:1121px">SENSITIVITIES</span>
    <span style="left:1241px">|</span>
    <span style="left:1263px">FAVOURITESS</span>
  </header>
  <nav class="dropdown"><div>Equities</div><div>Etfs</div><div>Pairs</div><div>Etf Pairs</div><div>Factors</div></nav>

  <div class="label" style="left:29px;top:121px">Quality &nbsp;&nbsp;<b>Threshold :</b></div>
  <div class="field" style="left:242px;top:119px;width:229px">-10</div>
  <div class="label" style="left:510px;top:121px">Abs. stat &nbsp;&nbsp;<b>Threshold :</b></div>
  <div class="field" style="left:733px;top:119px;width:229px">-10</div>
  <div class="export" style="left:458px;top:182px">
    <svg width="25" height="24" viewBox="0 0 25 24" fill="none" stroke="var(--icon)" stroke-width="2"><path d="M15 4H3v16h12"/><path d="M9 12h14M18 7l5 5-5 5"/></svg>Export
  </div>

  <table class="models" style="top:257px;width:1340px">
    <colgroup><col style="width:90px"><col style="width:134px"><col style="width:132px"><col style="width:97px"><col style="width:117px"><col style="width:98px"><col style="width:112px"><col style="width:112px"><col style="width:112px"><col style="width:112px"><col style="width:112px"><col style="width:112px"></colgroup>
    <thead><tr><th>ID</th><th>SECTOR</th><th>TIME</th><th>QUALITY</th><th>STAT 1</th><th>STAT 2</th><th>STAT 3</th><th>STAT 4</th><th>STAT 5</th><th>STAT 6</th><th>STAT 7</th><th>STAT 8</th></tr></thead>
    <tbody>
      <tr><td class="id">Model 1</td><td>Materials</td><td class="num">2019-07-03<br>12:15:00.000</td><td class="num">30.2288</td><td class="num">2.01574</td><td class="num">23.305</td><td class="num">-0.149368</td><td class="num">22.3054</td><td class="num">4.63714</td><td class="num">0.945706</td><td class="num">2.81949</td><td class="num">2.60858</td></tr>
      <tr><td class="id">Model 2</td><td>Industrials</td><td class="num">2019-07-03<br>12:15:00.000</td><td class="num">32.8694</td><td class="num">0.87307</td><td class="num">32.185</td><td class="num">-0.0336927</td><td class="num">33.9911</td><td class="num">11.5693</td><td class="num">-0.472968</td><td class="num">-0.830458</td><td class="num">6.80646</td></tr>
      <tr><td class="id">Model 3</td><td>Consumer<br>Discretionary</td><td class="num">2019-07-03<br>12:15:00.000</td><td class="num">30.2288</td><td class="num">-0.569222</td><td class="num">159.814</td><td class="num">0.0252328</td><td class="num">172.616</td><td class="num">10.2875</td><td class="num">-0.750396</td><td class="num">-0.385309</td><td class="num">4.69146</td></tr>
      <tr><td class="id">Model 4</td><td>Information<br>Technology</td><td class="num">2019-07-03<br>12:15:00.000</td><td class="num">45.6856</td><td class="num">0.412148</td><td class="num">202.488</td><td class="num">0.00849232</td><td class="num">205.834</td><td class="num">11.9094</td><td class="num">-0.137913</td><td class="num">0.449595</td><td class="num">3.85106</td></tr>
      <tr><td class="id">Model 5</td><td>Information<br>Technology</td><td class="num">2019-07-03<br>12:15:00.000</td><td class="num">75.7733</td><td class="num">7.06728</td><td class="num">188.605</td><td class="num">0.016913</td><td class="num">181.665</td><td class="num">3.82241</td><td class="num">0.981019</td><td class="num">1.29847</td><td class="num">3.34927</td></tr>
    </tbody>
  </table>

  <div class="footer" style="top:688px">© 2019 Pellworth. All Rights Reserved</div>
  <div class="code" style="left:1361px;top:692px">C37</div>
</section>

<section class="panel panel--factors">
  <header class="topbar">
    <span class="brand" style="left:28px">PELLWORTH</span>
    <span style="left:501px">QBOSS</span>
    <span style="left:590px">250D</span>
    <span style="left:666px">83D</span>
    <span style="left:732px">42D</span>
    <span style="left:1029px">MODELS</span>
    <span style="left:1110px">|</span>
    <span style="left:1131px">SENSITIVITIES</span>
    <span style="left:1251px">|</span>
    <span style="left:1273px">FAVOURITES</span>
  </header>

  <div class="label" style="left:38px;top:122px">Stat 1 <b>Threshold :</b></div>
  <div class="field" style="left:221px;top:120px;width:229px">-10</div>
  <div class="label" style="left:498px;top:122px">Stat 1 <b>Threshold :</b></div>
  <div class="field" style="left:681px;top:120px;width:229px">-10</div>
  <div class="label" style="left:951px;top:122px">Stat 1 <b>Threshold :</b></div>
  <div class="field" style="left:1134px;top:120px;width:229px">-10</div>
  <div class="export" style="left:658px;top:183px">
    <svg width="25" height="24" viewBox="0 0 25 24" fill="none" stroke="var(--icon)" stroke-width="2"><path d="M15 4H3v16h12"/><path d="M9 12h14M18 7l5 5-5 5"/></svg>Export
  </div>

  <table class="factors" style="top:250px;width:1337px">
    <colgroup><col style="width:145px"><col style="width:146px"><col style="width:170px"><col style="width:146px"><col style="width:146px"><col style="width:146px"><col style="width:146px"><col style="width:146px"><col style="width:146px"></colgroup>
    <thead><tr><th>FACTOR</th><th>ID</th><th>SECTOR</th><th>STAT 1</th><th>STAT 2</th><th>STAT 3</th><th>STAT 4</th><th>STAT 5</th><th>STAT 6</th></tr></thead>
    <tbody>
      <tr><td class="id">Factor 1</td><td class="id">Model 1</td><td>Materials</td><td class="num">-1.4</td><td class="num">0.1</td><td class="num">-3.1</td><td class="num">0.7</td><td class="num">30.2</td><td class="num">0.9</td></tr>
      <tr><td class="id">Factor 2</td><td class="id">Model 1</td><td>Materials</td><td class="num">2.8</td><td class="num">0.1</td><td class="num">6.1</td><td class="num">100</td><td class="num">30.2</td><td class="num">0.9</td></tr>
      <tr><td class="id">Factor 3</td><td class="id">Model 1</td><td>Materials</td><td class="num">-3.7</td><td class="num">2.7</td><td class="num">-7.2</td><td class="num">100</td><td class="num">30.2</td><td class="num">0.9</td></tr>
      <tr><td class="id">Factor 1</td><td class="id">Model 2</td><td>Industrials</td><td class="num">2.8</td><td class="num">0.2</td><td class="num">2.7</td><td class="num">0.5</td><td class="num">32.9</td><td class="num">-0.5</td></tr>
      <tr><td class="id">Factor 2</td><td class="id">Model 2</td><td>Industrials</td><td class="num">0.8</td><td class="num">0.3</td><td class="num">2.5</td><td class="num">0.5</td><td class="num">32.9</td><td class="num">-0.5</td></tr>
    </tbody>
  </table>

  <div class="footer" style="top:590px">© 2019 Pellworth. All Rights Reserved</div>
  <div class="code" style="left:1354px;top:594px;font-size:16px">C37</div>
</section>

</div>
</body>
</html>
```